Indy Film Production Company/Studio

We need a business card designed from an existing logo. We are a digital studio/production company that caters to creating genre entertainment, like Action, Horror, and martial arts. The card along with the logo will be used to Brand the company from letter heads to banners. The design will also be used for postcards and Brochures. It should be professional and masculine.
Updates

Thank you to all the designers who have participated. I'm narrowing down who it will be. Thank you again.

Target Market(s)

Investors, Networks, Producers, and actors

Industry/Entity Type

Film Production

Contact Information for Business Card

Teodoro Valbuena
Producer/Writer/Director
www.kestrelpicturehouse.example

Requirements
Must have
• Website address, Facebook icon and Twitter icon possibly in the back of the card.
Nice to have
• Logline of Company: Follow The Action.

```html
<!DOCTYPE html>
<html lang="en">
<head>
<meta charset="UTF-8">
<title>Kestrel Picture House — Business Card</title>
<link rel="stylesheet" href="https://fonts.googleapis.com/css2?family=Roboto:wght@400;500;900&display=swap">
<style>
  :root {
    --brand-red: #ea1f29;
    --brand-red-deep: #d3141e;
    --ink-dark: #3a3a3a;
    --ink-mid: #5c5c5c;
    --card-white: #ffffff;
    --divider: #dcdcdc;
    --band-grey: #cfcfcf;
    --stage: #ecebe8;
    --social-box: #2b2b2b;
  }
  * { box-sizing: border-box; margin: 0; padding: 0; }
  html, body {
    width: 1200px; height: 950px; overflow: hidden;
    background: var(--stage);
    font-family: "Roboto", Arial, sans-serif;
  }
  .sheet { position: relative; width: 1200px; height: 950px; }
  .card {
    position: absolute; left: 220px; width: 760px; height: 434px;
    box-shadow: 0 6px 18px rgba(0,0,0,0.18);
    overflow: hidden;
  }
  /* Front */
  .card--front { top: 30px; background: var(--brand-red); }
  .social-box {
    position: absolute; top: 20px; right: 22px;
    width: 62px; height: 30px; background: var(--social-box);
    display: flex; align-items: center; justify-content: center; gap: 8px;
  }
  .social-box span { width: 18px; height: 18px; background: #5a5a5a; }
  .front-logo {
    position: absolute; left: 0; right: 0; top: 150px; text-align: center;
  }
  .front-logo .wordmark {
    color: var(--card-white); font-weight: 900; font-size: 46px;
    letter-spacing: 2px; text-transform: uppercase; line-height: 1;
  }
  .front-logo .sub-url {
    margin-top: 12px; color: var(--card-white); font-size: 17px;
    letter-spacing: 2px; font-weight: 400;
  }
  .front-url {
    position: absolute; left: 0; right: 0; top: 300px; text-align: center;
    color: var(--card-white); font-size: 20px; letter-spacing: 3px;
  }
  /* Back */
  .card--back { top: 486px; background: var(--card-white); }
  .back-logo {
    position: absolute; left: 40px; top: 150px; width: 330px; text-align: center;
    color: var(--brand-red); font-weight: 900; font-size: 34px;
    line-height: 1.1; text-transform: uppercase; letter-spacing: 1px;
  }
  .divider {
    position: absolute; left: 395px; top: 40px; width: 1px; height: 290px;
    background: linear-gradient(to bottom, transparent, var(--divider) 20%, var(--divider) 80%, transparent);
  }
  .contact { position: absolute; left: 425px; top: 80px; right: 20px; }
  .contact .name { color: var(--brand-red); font-size: 24px; font-weight: 500; }
  .contact .role { color: var(--ink-dark); font-size: 18px; margin-top: 6px; }
  .contact ul { list-style: none; margin-top: 18px; }
  .contact li {
    display: flex; align-items: center; gap: 10px;
    color: var(--ink-mid); font-size: 15px; margin-bottom: 9px;
  }
  .contact li svg { flex: none; }
  .bottom-grey {
    position: absolute; left: 0; right: 0; bottom: 30px; height: 8px; background: var(--band-grey);
  }
  .bottom-band {
    position: absolute; left: 0; right: 0; bottom: 0; height: 30px; background: var(--brand-red-deep);
  }
</style>
</head>
<body>
<main class="sheet">
  <section class="card card--front" aria-label="Card front">
    <div class="social-box" aria-label="Social links"><span></span><span></span></div>
    <div class="front-logo">
      <div class="wordmark">Kestrel Picture House</div>
      <div class="sub-url">kestrelpicturehouse.example</div>
    </div>
    <div class="front-url">www.kestrelpicturehouse.example</div>
  </section>

  <section class="card card--back" aria-label="Card back">
    <div class="back-logo">Kestrel<br>Picture House</div>
    <div class="divider"></div>
    <div class="contact">
      <div class="name">Teodoro Valbuena</div>
      <div class="role">Producer/Writer/Director</div>
      <ul>
        <li>
          <svg width="16" height="16" viewBox="0 0 16 16" aria-hidden="true"><path fill="var(--brand-red)" d="M3 1h3l1 4-2 1c1 2 2 3 4 4l1-2 4 1v3c0 1-1 2-2 2C6 14 2 10 1 3c0-1 1-2 2-2z"/></svg>
          555 0142 7788
        </li>
        <li>
          <svg width="16" height="12" viewBox="0 0 16 12" aria-hidden="true"><rect width="16" height="12" rx="1" fill="var(--brand-red)"/><path d="M1 1l7 6 7-6" stroke="#fff" stroke-width="1.4" fill="none"/></svg>
          teodoro@kestrelpicturehouse.example
        </li>
        <li>
          <svg width="16" height="16" viewBox="0 0 16 16" aria-hidden="true"><circle cx="8" cy="8" r="8" fill="var(--brand-red)"/><path d="M8 4a3 3 0 0 1 3 3c0 2-3 5-3 5S5 9 5 7a3 3 0 0 1 3-3z" fill="#fff"/></svg>
          www.kestrelpicturehouse.example
        </li>
      </ul>
    </div>
    <div class="bottom-grey"></div>
    <div class="bottom-band"></div>
  </section>
</main>
</body>
</html>
```